KCA Waltz of our luminaries

My nonprofit social service agency is having a fun gala based on the TV show waltz of the luminaries, and we need the key design for an invitation. The event is a dinner and will have 7 local well-known people dance in a contest-like setting with a nationally known host. This does not need to be the final invitation (RSVP, list of dancers/hosts, etc.). All I need at this point is a great design for the cover to give this event an identity and entice people to attend and/or donate to the cause! Though our logo colors are blue/green/burgandy, this can use black/gold/silver/white as well. Our website is www.kcaohvalley.org if that helps explain who we are.

Also, it can be abstract. And it does not have to include ballroom dancers if the word mark or other graphics are eye catching.

Target Market(s)

Donors, upscale, higher income,45-70, men and women (though women will more likely make the decision to attend)

Industry/Entity Type

Tv

Requirements
Must have
• The wording to be incorporated into the invitation cover is:
Kindred Care Alliance
Celebrates Rising Strong Through Years with
Waltz of the Luminaries
hosted by Host Name (will give the final name when confirmed)

Saturday, November 8, 2014
7 pm
Marlowe Cincinnati Tidewater Court
Nice to have
• I'd like to see something other than ballroom dancers just to give my committee some options. Is it possible to show footprints of dancers (man's shoe with woman's high heels) as the design element? Something that can be used across the invite (rsvp card).
Should not have
• You have free range to create and have fun! If you use our logo colors, either choose one color as the focus, or just be sure to focus on green and burgandy together

```html
<!DOCTYPE html>
<html lang="en">
<head>
<meta charset="utf-8">
<title>Kindred Care Alliance – Waltz of our Luminaries</title>
<link href="https://fonts.googleapis.com/css2?family=Arimo:wght@400&family=Great+Vibes&display=swap" rel="stylesheet">
<style>
  :root {
    --stage: #000000;
    --paper: #ffffff;
    --ink: #111111;
    --blue: #0b67d0;
    --burgundy: #9c3a6b;
    --green: #3a9a3a;
    --shoe-dark: #1c1c1c;
    --shoe-mid: #5a5a5a;
  }
  * { box-sizing: border-box; margin: 0; padding: 0; }
  html, body {
    width: 1200px; height: 900px; overflow: hidden;
    background: var(--stage);
  }
  .invitation-cover {
    position: absolute; left: 310px; top: 38px;
    width: 581px; height: 825px;
    overflow: hidden;
    background: var(--paper);
    font-family: "Arimo", Arial, sans-serif;
    color: var(--ink);
  }
  .agency-name {
    position: absolute; left: 0; right: 0; top: 45px;
    display: flex; align-items: center; justify-content: center; gap: 10px;
    font-size: 24px; line-height: 30px; color: var(--blue);
  }
  .agency-dot {
    width: 26px; height: 26px; border-radius: 50%;
    background: var(--burgundy);
  }
  .tagline {
    position: absolute; left: 0; right: 0; top: 101px;
    text-align: center; font-size: 16px; line-height: 20px;
  }
  .event-title { font-weight: 400; }
  .title-script {
    position: absolute; font-family: "Great Vibes", cursive;
    font-weight: 400; line-height: 1; white-space: nowrap;
  }
  .title-waltz { left: 30px; top: 128px; font-size: 124px; color: var(--blue); }
  .title-of {
    position: absolute; left: 262px; top: 262px;
    font-size: 26px; font-weight: 400; color: var(--burgundy); white-space: nowrap;
  }
  .title-luminaries { left: 352px; top: 236px; font-size: 58px; color: var(--green); }
  .shoe-art {
    position: absolute; border-radius: 40px 40px 10px 10px;
    background: linear-gradient(180deg, rgba(255,255,255,0) 0%, var(--shoe-mid) 55%, var(--shoe-dark) 100%);
    opacity: 0.85;
  }
  .shoe-boot { left: 150px; top: 310px; width: 128px; height: 255px; }
  .shoe-oxford { left: 330px; top: 330px; width: 112px; height: 370px; }
  .hosted-by {
    position: absolute; left: 41px; top: 640px; font-size: 28px; line-height: 32px;
  }
  .host-name {
    position: absolute; left: 41px; top: 678px; font-size: 22px; line-height: 26px; letter-spacing: 1px;
  }
  .event-details {
    position: absolute; left: 0; top: 726px; list-style: none;
  }
  .event-details li {
    display: flex; align-items: center; height: 27px; font-size: 20px;
  }
  .event-details .swatch { width: 30px; height: 20px; margin-right: 11px; }
  .swatch-blue { background: var(--blue); }
  .swatch-burgundy { background: var(--burgundy); }
  .swatch-green { background: var(--green); }
</style>
</head>
<body>
  <main class="invitation-cover">
    <div class="agency-name"><span class="agency-dot"></span><span>Kindred Care Alliance...</span></div>
    <p class="tagline">Celebrates Rising Strong Through Years</p>

    <h1 class="event-title">
      <span class="title-script title-waltz">Waltz</span>
      <span class="title-of">of our</span>
      <span class="title-script title-luminaries">Luminaries</span>
    </h1>

    <div class="shoe-art shoe-boot" role="img" aria-label="Black heeled dance boot hanging from a ribbon tied to the title"></div>
    <div class="shoe-art shoe-oxford" role="img" aria-label="Black men's dance shoe hanging from a ribbon tied to the title"></div>

    <p class="hosted-by">hosted by</p>
    <p class="host-name">XXXXX XXXXXX</p>

    <ul class="event-details">
      <li><span class="swatch swatch-blue"></span>Saturday, November 8, 2014</li>
      <li><span class="swatch swatch-burgundy"></span>7 pm</li>
      <li><span class="swatch swatch-green"></span>Marlowe Cincinnati Tidewater Court</li>
    </ul>
  </main>
</body>
</html>
```